Presentation Brochure and Sample Box Design for Varnex Board

Varnex Board is our range of aluminium composite panel that our company supplies to the signage and shop fitting industries.
the range is divided into 3 sections: Signage Grade - Light Commercial Grade and Commercial Grade.
We require an, A4 double-sided folding brochure (swatch book) that folds 3 ways, opening once and then a second time to lay out 3 pages flat.

There should be a front and back cover.

The inside cover should be reserved with text blocks for written information about the composite panel.

The opposite page on the right when you first open the brochure should have all our Commercial Grade colours, which are the timber finishes and the 4mm black, white and metallic silver.

When the brochure is folded out a second time, showing all three inside pages flat, the two inside pages on the right (next to the inside cover with the written information) should show all our Signage Grade colours, followed by the Light Commercial Grade colours.
Each colour in each section should have the product code beneath the swatch.

This brochure should have a modern and professional feel suitable for presenting to signees, shop fitters and interiors designers.

We also require a box design to contain aluminium composite panel samples of all the colours in the range.

Please refer to the template attached for the box dimensions and layout.

The box should tie in with the brochure as a complete package with a modern and professional look suitable for presenting to shop fitters and interior designers.

Finally we require a small label sticker to be stuck on the back of each sample. On the sticker should be the Varnex Board logo, a space to put the product code for the sample colour and the phone number 1300 584 906.

To summarise, this package project includes:
1 tri-folding A4 brochure,
1 sample box package design
1 sample sticker label.

Please refer to the attachments for the Varnex Board logo in two formats - the colour swatch book and template for the sample box.
The Logo may be shown with either the original blue text or with the text in white. The blue icon colour should not change.

Target Market(s)

Signage, shop fitting and interior design

Font styles to use
Serif
Sans Serif

Requirements
Must have
• A modern, neat and professional upmarket look suitable for presenting to shop fitters and interior designers.
Nice to have
• A slick and classy look that makes you want to take home the box or brochure even if you're not interested in the product.
Should not have
• A cheap, untidy, low market look with too many colours.

```html
<!DOCTYPE html>
<html lang="en">
<head>
<meta charset="utf-8">
<title>Varnex Board – Swatch Book Spreads</title>
<link href="https://fonts.googleapis.com/css2?family=Josefin+Sans:wght@400;600;700&family=Lato:wght@400;700;900&display=swap" rel="stylesheet">
<style>
  :root{
    --stage:#6d6d6d;
    --navy:#1b2660;
    --navy-ink:#1f2a6b;
    --blue:#1e88d0;
    --paper:#ffffff;
    --paper-soft:#efefef;
    --rule:#d6d6d6;
    --frame:#bdbdbd;
    --ink:#2a2a2a;
    --white:#ffffff;
    --undercoat:#e3e5e9;
    --grey:#c8c8c8;
    --black:#0c0c0c;
    --black-soft:#231f20;
    --metal-beige:#d8d5c8;
    --red:#e2231a; --yellow:#ffe000; --process-blue:#0a7fc4; --reflex-blue:#262f86;
    --forest:#1f4d35; --heritage:#7a1b2a; --orange:#ef5a24; --navy-blue:#1f2a55;
    --emerald:#0a9a4a; --steel:#252830;
    --brush-silver:#b9bdc2; --raw-al:#cfd0d2; --copper:#b57a58; --gold:#9c8a55;
    --rust:#8b2a1c; --emboss:#c9c9c9;
    --wattle:#8a4a26; --allspice:#6b3a22; --oak:#d7a96a; --walnut:#7a3f25; --wenge:#4a3226; --gum:#9a5a3a;
  }
  *{margin:0;padding:0;box-sizing:border-box}
  html,body{width:756px;height:1200px;overflow:hidden;background:var(--stage)}
  body{position:relative;font-family:'Lato',sans-serif;color:var(--ink)}

  .spread{position:absolute;left:20px;width:716px;height:337px;display:flex;box-shadow:0 2px 10px rgba(0,0,0,.25)}
  .spread--outside{top:243px}
  .spread--inside{top:620px}
  .panel{position:relative;width:238.67px;height:337px;overflow:hidden}
  .panel--soft{background:linear-gradient(160deg,var(--paper) 0%,var(--paper-soft) 100%)}
  .panel--white{background:var(--paper)}
  .panel--navy{background:var(--navy)}

  .frame{position:absolute;left:11px;top:11px;width:216px;height:315px;border:1.5px solid var(--frame);border-radius:4px}

  .section-title{position:absolute;left:20px;font-family:'Josefin Sans',sans-serif;font-weight:700;font-size:8px;letter-spacing:.2px;color:var(--blue)}
  .section-title--light{color:var(--white);left:16px;font-size:8.2px}
  .section-rule{position:absolute;left:20px;width:190px;height:.6px;background:var(--rule)}
  .section-rule--light{left:16px;width:205px;background:rgba(255,255,255,.15)}

  .swatches{position:absolute;display:grid;grid-template-columns:repeat(8,22px);column-gap:4.4px;row-gap:4.4px}
  .swatches--commercial{grid-template-columns:repeat(4,30px);column-gap:6px;row-gap:5.5px}
  .sw{position:relative;width:22px;height:22px;background:var(--white);box-shadow:0 .5px 1.5px rgba(0,0,0,.25)}
  .swatches--commercial .sw{width:30px;height:30px}
  .sw span{position:absolute;left:0;right:0;bottom:2.5px;text-align:center;font-size:2.6px;font-weight:900;line-height:1.05;color:#333;text-transform:uppercase}
  .swatches--commercial .sw span{font-size:3.2px;bottom:4px}
  .sw.on-dark span{color:var(--white)}

  .f-undercoat{background:var(--undercoat)} .f-grey{background:var(--grey)}
  .f-black{background:var(--black)} .f-black-soft{background:var(--black-soft)}
  .f-metal{background:var(--metal-beige)}
  .f-red{background:var(--red)} .f-yellow{background:var(--yellow)} .f-pblue{background:var(--process-blue)}
  .f-rblue{background:var(--reflex-blue)} .f-forest{background:var(--forest)} .f-heritage{background:var(--heritage)}
  .f-orange{background:var(--orange)} .f-navyblue{background:var(--navy-blue)} .f-emerald{background:var(--emerald)}
  .f-steel{background:var(--steel)} .f-brush{background:linear-gradient(135deg,#d3d6da,var(--brush-silver))}
  .f-raw{background:var(--raw-al)} .f-copper{background:var(--copper)} .f-gold{background:var(--gold)}
  .f-rust{background:var(--rust)} .f-emboss{background:var(--emboss)}
  .f-wattle{background:linear-gradient(90deg,var(--wattle),#b06a3c,var(--wattle))}
  .f-allspice{background:linear-gradient(90deg,var(--allspice),#8d5233,var(--allspice))}
  .f-oak{background:linear-gradient(90deg,var(--oak),#e6c08a,var(--oak))}
  .f-walnut{background:linear-gradient(90deg,var(--walnut),#99533a,var(--walnut))}
  .f-wenge{background:linear-gradient(90deg,var(--wenge),#62463a,var(--wenge))}
  .f-gum{background:linear-gradient(90deg,var(--gum),#b87552,var(--gum))}

  .brand-mark{position:absolute;font-family:'Josefin Sans',sans-serif;font-weight:600;letter-spacing:.8px;color:var(--navy-ink);white-space:nowrap}
  .brand-mark--small{font-size:6px}
  .brand-mark--light{color:var(--white)}

  .contact-title{position:absolute;left:22px;top:20px;font-family:'Josefin Sans',sans-serif;font-weight:700;font-size:5.6px;color:var(--navy-ink);letter-spacing:.2px}
  .contact-list{position:absolute;left:22px;top:30px;list-style:none;font-size:5px;line-height:7px;color:var(--navy-ink)}
  .contact-list li{display:flex;align-items:flex-start;gap:3px}
  .contact-list .dot{flex:none;width:4.5px;height:4.5px;margin-top:1px;border-radius:50%;background:var(--blue)}
  .contact-list .cont{padding-left:7.5px}

  .wordmark-vertical{position:absolute;left:0;top:0}

  .photo{position:absolute}
  .photo--tower-bw{left:14px;top:112px;width:225px;height:225px;background:radial-gradient(circle at 70% 40%,#e0e0e0 0%,#8a8a8a 35%,#1f1f1f 70%,#dcdcdc 100%)}
  .photo--tower-blue{left:77px;top:0;width:143px;height:154px;background:linear-gradient(170deg,#c7d6ef 0%,#5d7fbd 40%,#1c3a7a 75%,#0f2452 100%)}

  .side-strip{position:absolute;left:0;top:0;width:77px;height:337px;background:#ededed}

  .about-title{position:absolute;left:77px;top:166px;font-family:'Josefin Sans',sans-serif;font-weight:700;font-size:17px;color:var(--navy-ink);letter-spacing:.2px}
  .about-copy{position:absolute;left:77px;top:194px;width:143px;font-size:5.5px;line-height:7.6px;text-align:justify;color:var(--navy-ink)}
  .about-copy p+p{margin-top:7px}
</style>
</head>
<body>

<!-- Outside spread -->
<section class="spread spread--outside">
  <!-- Commercial grade flap -->
  <div class="panel panel--soft">
    <div class="frame"></div>
    <h2 class="section-title" style="top:22px">COMMERCIAL GRADE</h2>
    <div class="section-rule" style="top:32px"></div>
    <div class="swatches swatches--commercial" style="left:20px;top:45px">
      <div class="sw f-wattle on-dark"><span>Golden<br>Wattle</span></div>
      <div class="sw"><span>High Gloss<br>White</span></div>
      <div class="sw f-walnut on-dark"><span>Walnut</span></div>
      <div class="sw"><span>High Gloss<br>White</span></div>
      <div class="sw f-allspice on-dark"><span>Vintage<br>Allspice</span></div>
      <div class="sw"><span>High Gloss<br>White</span></div>
      <div class="sw f-wenge on-dark"><span>Wenge<br>Dark</span></div>
      <div class="sw"><span>High Gloss<br>White</span></div>
      <div class="sw f-oak on-dark"><span>Sorrento<br>Oak</span></div>
      <div class="sw"><span>High Gloss<br>White</span></div>
      <div class="sw f-gum on-dark"><span>Sydney<br>Spotted Gum</span></div>
      <div class="sw"><span>High Gloss<br>White</span></div>
    </div>

    <h2 class="section-title" style="top:160px">COMMERCIAL GRADE 4MM</h2>
    <div class="section-rule" style="top:170px"></div>
    <div class="swatches swatches--commercial" style="left:20px;top:184px">
      <div class="sw f-metal"><span>PVDF Metallic<br>Silver</span></div>
      <div class="sw"><span>High Gloss<br>White</span></div>
      <div class="sw"><span>High Gloss<br>White</span></div>
      <div class="sw"><span>PVDF Matte<br>White</span></div>
      <div class="sw f-black on-dark"><span>High Gloss<br>Black</span></div>
      <div class="sw f-black-soft on-dark"><span>PVDF Matte<br>Black</span></div>
      <div class="sw f-black on-dark"><span>PVDF Metallic<br>Black</span></div>
      <div class="sw f-grey"><span>Undercoat</span></div>
      <div class="sw f-black on-dark"><span>Feve Semi Gloss<br>Black</span></div>
      <div class="sw f-grey"><span>Feve Semi Gloss<br>White</span></div>
    </div>
    <div class="brand-mark brand-mark--small" style="left:96px;top:306px">VARNEX BOARD</div>
  </div>

  <!-- Back cover -->
  <div class="panel panel--white">
    <h3 class="contact-title">CORPORATE ADDRESS</h3>
    <ul class="contact-list">
      <li><i class="dot"></i>48 Kestrel Row Ste 9</li>
      <li class="cont">Marlow Heights, WA 123456</li>
      <li><i class="dot"></i>1300 584 906</li>
      <li><i class="dot"></i>hello@varnexboard.com</li>
      <li><i class="dot"></i>www.varnexboard.com</li>
    </ul>
    <svg class="wordmark-vertical" width="239" height="337" viewBox="0 0 239 337">
      <text transform="translate(205,320) rotate(-90)" x="0" y="0" textLength="298" lengthAdjust="spacing"
            font-family="'Josefin Sans', sans-serif" font-weight="600" font-size="40" fill="#1f2a6b">VARNEX BOARD</text>
    </svg>
  </div>

  <!-- Front cover -->
  <div class="panel panel--soft">
    <div class="brand-mark" style="left:0;right:0;top:62px;text-align:center;font-size:11px">VARNEX BOARD</div>
    <div class="photo photo--tower-bw" role="img" aria-label="Black and white photograph of a curving high-rise tower with wave-like balconies"></div>
  </div>
</section>

<!-- Inside spread -->
<section class="spread spread--inside">
  <!-- Inside cover -->
  <div class="panel panel--white">
    <div class="side-strip"></div>
    <svg class="wordmark-vertical" width="239" height="337" viewBox="0 0 239 337">
      <text transform="translate(42,316) rotate(-90)" x="0" y="0" textLength="296" lengthAdjust="spacing"
            font-family="'Josefin Sans', sans-serif" font-weight="600" font-size="40" fill="#ffffff">VARNEX BOARD</text>
    </svg>
    <div class="photo photo--tower-blue" role="img" aria-label="Photograph looking up at a blue glass skyscraper against the sky"></div>
    <h1 class="about-title">VARNEX BOARD</h1>
    <div class="about-copy">
      <p><b>Varnex Board</b> is an aluminium composite panel made for signage, shop fitting and interior work. Two skins of coil-coated aluminium are bonded to a solid core, giving a flat, rigid sheet that cuts, routes and folds cleanly, and holds its colour for years outdoors.</p>
      <p>Every grade in this book is shown at true finish. Ask your representative for a sample box to see each colour under your own light before you specify a project.</p>
    </div>
    <div class="brand-mark brand-mark--small" style="left:170px;top:312px">VARNEX BOARD</div>
  </div>

  <!-- Signage grade -->
  <div class="panel panel--navy">
    <h2 class="section-title section-title--light" style="top:13px">SIGNAGE GRADE 2MM</h2>
    <div class="section-rule section-rule--light" style="top:25px"></div>
    <div class="swatches" style="left:16px;top:31px">
      <div class="sw"><span>Matte<br>White</span></div>
      <div class="sw f-undercoat"><span>Undercoat</span></div>
      <div class="sw"><span>Matte<br>White</span></div>
      <div class="sw"><span>Matte White<br>Digital</span></div>
      <div class="sw"><span>High Gloss<br>White</span></div>
      <div class="sw"><span>Matte<br>White</span></div>
      <div class="sw"><span>Matte White<br>Digital</span></div>
      <div class="sw"><span>Matte White<br>Digital</span></div>
      <div class="sw"><span>Matte<br>White</span></div>
      <div class="sw f-black-soft on-dark"><span>Matte<br>Black</span></div>
      <div class="sw f-black-soft on-dark"><span>Matte<br>Black</span></div>
      <div class="sw f-black-soft on-dark"><span>Matte<br>Black</span></div>
      <div class="sw"><span>Matte White<br>Digital</span></div>
      <div class="sw"><span>Undercoat<br>Matte White</span></div>
      <div class="sw"><span>Gloss<br>White</span></div>
      <div class="sw"><span>Matte White<br>Digital</span></div>
    </div>

    <h2 class="section-title section-title--light" style="top:91px">SIGNAGE GRADE 3MM</h2>
    <div class="section-rule section-rule--light" style="top:103px"></div>
    <div class="swatches" style="left:16px;top:109px">
      <div class="sw f-black on-dark"><span>High Gloss<br>Black</span></div>
      <div class="sw f-black on-dark"><span>High Gloss<br>Black</span></div>
      <div class="sw f-black on-dark"><span>High Gloss<br>Black</span></div>
      <div class="sw f-black-soft on-dark"><span>Matte<br>Black</span></div>
      <div class="sw f-black-soft on-dark"><span>Matte<br>Black</span></div>
      <div class="sw f-black-soft on-dark"><span>Matte<br>Black</span></div>
      <div class="sw"><span>Semi-Gloss<br>White</span></div>
      <div class="sw f-undercoat"><span>Undercoat</span></div>

      <div class="sw"><span>Semi-Gloss<br>White</span></div>
      <div class="sw"><span>Semi-Gloss<br>White</span></div>
      <div class="sw"><span>Matte<br>White</span></div>
      <div class="sw f-black-soft on-dark"><span>Matte<br>Black</span></div>
      <div class="sw"><span>Gloss<br>White</span></div>
      <div class="sw f-undercoat"><span>Undercoat</span></div>
      <div class="sw f-undercoat"><span>Undercoat</span></div>
      <div class="sw f-undercoat"><span>Undercoat</span></div>

      <div class="sw"><span>High Gloss<br>White</span></div>
      <div class="sw"><span>High Gloss<br>White</span></div>
      <div class="sw"><span>High Gloss<br>White</span></div>
      <div class="sw"><span>High Gloss<br>Black</span></div>
      <div class="sw f-black on-dark"><span>High Gloss<br>Black</span></div>
      <div class="sw"><span>High Gloss<br>White</span></div>
      <div class="sw f-brush"><span>Brush Silver</span></div>
      <div class="sw f-raw"><span>Raw<br>Aluminium</span></div>

      <div class="sw f-red on-dark"><span>High Gloss<br>Red</span></div>
      <div class="sw"><span>High Gloss<br>White</span></div>
      <div class="sw f-yellow"><span>High Gloss<br>Yellow</span></div>
      <div class="sw"><span>High Gloss<br>White</span></div>
      <div class="sw f-pblue on-dark"><span>High Gloss<br>Process Blue</span></div>
      <div class="sw"><span>High Gloss<br>White</span></div>
      <div class="sw f-rblue on-dark"><span>High Gloss<br>Reflex Blue</span></div>
      <div class="sw"><span>High Gloss<br>White</span></div>

      <div class="sw f-forest on-dark"><span>High Gloss<br>Forest Green</span></div>
      <div class="sw"><span>High Gloss<br>White</span></div>
      <div class="sw f-heritage on-dark"><span>High Gloss<br>Heritage Red</span></div>
      <div class="sw"><span>High Gloss<br>White</span></div>
      <div class="sw f-orange on-dark"><span>High Gloss<br>Orange</span></div>
      <div class="sw"><span>High Gloss<br>White</span></div>
      <div class="sw f-navyblue on-dark"><span>High Gloss<br>Navy Blue</span></div>
      <div class="sw"><span>High Gloss<br>White</span></div>

      <div class="sw f-metal on-dark"><span>Metallic<br>Charcoal</span></div>
      <div class="sw"><span>High Gloss<br>White</span></div>
      <div class="sw f-emerald on-dark"><span>High Gloss<br>Emerald Green</span></div>
      <div class="sw"><span>High Gloss<br>White</span></div>
      <div class="sw f-metal on-dark"><span>Metallic<br>Silver</span></div>
      <div class="sw"><span>High Gloss<br>White</span></div>
      <div class="sw f-steel on-dark"><span>High Gloss<br>Steel Grey</span></div>
      <div class="sw"><span>High Gloss<br>White</span></div>
    </div>

    <h2 class="section-title section-title--light" style="top:275px">SIGNAGE GRADE 4MM</h2>
    <div class="section-rule section-rule--light" style="top:287px"></div>
    <div class="swatches" style="left:16px;top:293px">
      <div class="sw"><span>Matte<br>White</span></div>
      <div class="sw"><span>Matte<br>Black</span></div>
      <div class="sw"><span>Undercoat</span></div>
      <div class="sw"><span>Undercoat</span></div>
    </div>
    <div class="brand-mark brand-mark--small brand-mark--light" style="left:175px;top:312px">VARNEX BOARD</div>
  </div>

  <!-- Light commercial grade -->
  <div class="panel panel--navy">
    <h2 class="section-title section-title--light" style="top:13px">LIGHT COMMERCIAL GRADE 3MM</h2>
    <div class="section-rule section-rule--light" style="top:25px"></div>
    <div class="swatches" style="left:16px;top:31px">
      <div class="sw"><span>High Gloss<br>White</span></div>
      <div class="sw"><span>Matte<br>White</span></div>
      <div class="sw"><span>High Gloss<br>White</span></div>
      <div class="sw f-black on-dark"><span>High Gloss<br>Black</span></div>
      <div class="sw f-black on-dark"><span>High Gloss<br>Black</span></div>
      <div class="sw f-black-soft on-dark"><span>Matte<br>Black</span></div>
    </div>

    <h2 class="section-title section-title--light" style="top:69px">LIGHT COMMERCIAL GRADE OVERSIZED</h2>
    <div class="section-rule section-rule--light" style="top:80px"></div>
    <div class="swatches" style="left:16px;top:86px">
      <div class="sw"><span>High Gloss<br>White</span></div>
      <div class="sw"><span>Matte<br>White</span></div>
    </div>

    <h2 class="section-title section-title--light" style="top:118px">LIGHT COMMERCIAL GRADE SPECIALTY SURFACES</h2>
    <div class="section-rule section-rule--light" style="top:130px"></div>
    <div class="swatches" style="left:16px;top:136px">
      <div class="sw"><span>Mirror<br>Gold</span></div>
      <div class="sw f-grey"><span>Undercoat</span></div>
      <div class="sw f-raw"><span>Mirror<br>Silver</span></div>
      <div class="sw f-grey"><span>Undercoat</span></div>
      <div class="sw f-brush"><span>Brush<br>Silver</span></div>
      <div class="sw f-raw"><span>Raw<br>Aluminium</span></div>

      <div class="sw f-copper"><span>Brush<br>Copper</span></div>
      <div class="sw f-gold"><span>Brush<br>Gold</span></div>
      <div class="sw f-emboss"><span>Stucco<br>Embossed</span></div>
      <div class="sw f-raw"><span>Raw<br>Aluminium</span></div>
      <div class="sw f-brush"><span>Diamond Plate<br>Embossed</span></div>
      <div class="sw f-raw"><span>Raw<br>Aluminium</span></div>

      <div class="sw f-rust on-dark"><span>Textured<br>Rust</span></div>
      <div class="sw f-grey"><span>Undercoat</span></div>
      <div class="sw"><span>Mirror<br>Anthracite<br>Silver</span></div>
      <div class="sw f-grey"><span>Undercoat</span></div>
      <div class="sw f-brush"><span>Brush<br>Stainless Steel</span></div>
      <div class="sw"><span>Stainless<br>Steel</span></div>
    </div>
    <div class="brand-mark brand-mark--small brand-mark--light" style="left:175px;top:312px">VARNEX BOARD</div>
  </div>
</section>

</body>
</html>
```